Beacon Advisory Website

I currently have a website www.beaconadvisoryinc.com. We are a IT Consulting Company. Our website will pretty much tell out our services. I am looking to enhance my website and make it look more professional. Looking for very classy and Contemporary look and design for my website.

It Company

```html
<!DOCTYPE html>
<html lang="en">
<head>
<meta charset="utf-8">
<title>Beacon Advisory – IT Consulting</title>
<link href="https://fonts.googleapis.com/css2?family=Open+Sans:ital,wght@0,400;0,600;0,700;1,400&family=Raleway:wght@300;400;600;700&display=swap" rel="stylesheet">
<style>
:root{
  --navy:#1a4e8a;
  --blue:#1565b0;
  --bright:#1e9ad6;
  --cyan:#23b2ea;
  --deep:#12518f;
  --darkbar:#0f3f73;
  --grey:#e8ebee;
  --text:#555a60;
  --dark:#222;
  --white:#fff;
}
*{margin:0;padding:0;box-sizing:border-box}
html,body{width:682px;height:1200px;overflow:hidden;background:var(--white)}
body{font-family:"Open Sans",Arial,sans-serif;color:var(--text);position:relative}
.abs{position:absolute}
section,header,nav,footer{position:absolute;left:0;width:682px}

/* header */
.site-header{top:0;height:50px;background:linear-gradient(#fdfdfd,#eef0f2);border-top:2px solid var(--blue)}
.brand{left:60px;top:12px;display:flex;align-items:center;gap:6px}
.brand-mark{width:22px;height:22px;background:var(--blue);border-radius:3px}
.brand-name{font-family:"Raleway",sans-serif;font-weight:700;font-size:12px;color:var(--blue);letter-spacing:.5px;line-height:1.05}
.contact-chip{top:12px;display:flex;gap:7px;align-items:center}
.chip-icon{width:20px;height:20px;border-radius:50%;background:var(--blue);display:flex;align-items:center;justify-content:center}
.chip-label{font-size:6.5px;font-weight:700;color:var(--blue);display:block}
.chip-value{font-size:8px;color:#555}

/* nav */
.main-nav{top:50px;height:25px;background:linear-gradient(var(--bright),var(--blue))}
.main-nav ul{list-style:none}
.main-nav li{position:absolute;top:0;height:25px;line-height:25px;font-size:7.3px;font-weight:700;color:var(--white);text-align:center}
.main-nav li.active{background:var(--cyan);width:63px;left:61px}
.nav-sep{position:absolute;top:4px;width:1px;height:17px;background:rgba(255,255,255,.25)}

/* hero */
.hero{top:75px;height:212px;overflow:hidden}
.hero-photo{position:absolute;inset:0;background:linear-gradient(100deg,#eef2f6 0%,#cfd9e3 38%,#5a7898 58%,#1d3552 72%,#d9e0e8 88%,#f0f2f5 100%)}
.hero-title{position:absolute;left:61px;top:66px;font-family:"Raleway",sans-serif;font-weight:700;font-size:14.4px;line-height:18.6px;color:var(--navy);text-transform:uppercase}
.btn-more{position:absolute;left:61px;top:137px;width:70px;height:23px;background:var(--cyan);color:var(--white);font-size:7px;font-weight:700;line-height:23px;text-align:center}

/* welcome */
.welcome{top:287px;height:109px;background:linear-gradient(90deg,#1b9bd6,#30b3e6 50%,#1d8fcc);text-align:center;color:var(--white)}
.welcome h1{font-family:"Raleway",sans-serif;font-weight:400;font-size:17px;margin-top:12px}
.welcome-caret{position:absolute;left:335px;top:36px;width:0;height:0;border-left:6px solid transparent;border-right:6px solid transparent;border-top:6px solid var(--white)}
.welcome p{font-size:6.9px;line-height:12.6px;width:560px;margin:13px auto 0}
.welcome-toggle{position:absolute;left:329px;top:95px;width:24px;height:14px;background:#2b2f33;border-radius:2px 2px 0 0;color:var(--white);font-size:13px;line-height:14px;font-weight:700}

/* features */
.features{top:396px;height:207px;background:var(--white)}
.feature{position:absolute;top:0;width:180px;text-align:center}
.feature svg{display:block;margin:0 auto}
.feature h3{font-family:"Raleway",sans-serif;font-size:9.5px;font-weight:700;color:var(--dark);margin-top:7px;letter-spacing:.2px}
.feature.highlight h3{color:var(--bright)}
.feature p{font-size:6.9px;line-height:9.6px;margin-top:5px;padding:0 6px}

/* services */
.services{top:603px;height:182px;background:var(--grey)}
.section-title{font-family:"Raleway",sans-serif;font-weight:400;font-size:18px;color:var(--dark);text-align:center}
.section-title span{color:var(--bright)}
.title-rule{position:absolute;left:254px;width:174px;height:1px;background:#c9ccd0}
.title-dot{position:absolute;left:336px;width:9px;height:9px;border-radius:2px;background:var(--bright)}
.service-card{position:absolute;top:63px;width:167px;height:95px;overflow:hidden}
.card-photo{position:absolute;inset:0}
.card-label{position:absolute;left:0;bottom:0;width:100%;height:19px;background:rgba(21,80,150,.85);color:var(--white);font-family:"Raleway",sans-serif;font-size:11px;text-align:center;line-height:19px}
.card-feature{background:var(--deep);color:var(--white);text-align:center;padding:14px 8px 0}
.card-feature h4{font-family:"Raleway",sans-serif;font-size:11px;font-weight:600}
.card-feature p{font-size:6px;line-height:9.8px;font-weight:600;margin-top:5px}
.card-feature .link{font-size:6px;font-weight:700;margin-top:4px;display:block}

/* testimonial */
.testimonial{top:785px;height:175px}
.avatar{position:absolute;left:71px;top:72px;width:80px;height:80px;border-radius:50%;border:3px solid #d6dadd;background:radial-gradient(circle at 50% 40%,#c7a08a,#5a6f86 70%)}
.quote{position:absolute;left:166px;top:64px;width:454px;font-style:italic;font-size:7.2px;line-height:13.8px;text-align:center;color:#666}
.quote-mark{font-family:Georgia,serif;font-size:18px;color:#b8bcc0;font-style:normal;position:absolute}
.quote-rule{position:absolute;left:168px;top:132px;width:452px;height:1px;background:#dfe2e4}
.author{position:absolute;left:226px;top:143px;font-size:7px;font-weight:600;color:var(--blue)}
.dots{position:absolute;left:530px;top:145px;display:flex;gap:3px}
.dots i{width:5px;height:5px;border-radius:50%;background:#c8cbcf;display:block}
.dots i.on{background:var(--bright)}

/* footer */
.site-footer{top:920px;height:280px}
.footer-wave{position:absolute;left:0;top:0}
.footer-col{position:absolute;top:118px;color:var(--white)}
.footer-col h5{font-family:"Open Sans",sans-serif;font-size:10px;font-weight:600;margin-bottom:12px}
.quick-links{list-style:none;font-size:6.8px}
.quick-links li{margin-bottom:13.5px}
.quick-links li::before{content:"•";margin-right:7px}
.contact-row{display:flex;gap:8px;font-size:6.5px;line-height:9.5px;margin-bottom:9px}
.contact-row svg{flex:none;margin-top:1px}
.field{display:block;width:153px;height:19px;border:1px solid rgba(255,255,255,.7);border-radius:2px;font-size:6.8px;padding:4px 7px;margin-bottom:4px;color:var(--white)}
.field.tall{height:34px}
.submit{display:block;width:59px;height:19px;background:#e6e8ea;border-radius:2px;color:#333;font-size:7.5px;text-align:center;line-height:19px;margin-top:9px}
.col-divider{position:absolute;top:112px;width:1px;height:140px;background:rgba(255,255,255,.15)}
.footer-brand{position:absolute;left:505px;top:112px;display:flex;align-items:center;gap:6px}
.footer-brand .brand-mark{background:var(--white)}
.footer-brand .brand-name{color:var(--white)}
.social{position:absolute;left:511px;top:198px;display:flex;gap:8px}
.social i{display:block;width:17px;height:17px;border-radius:2px}
.copyright{position:absolute;left:0;top:258px;width:682px;height:22px;background:var(--darkbar);color:#d8e3ef;font-size:7px;text-align:center;line-height:22px}
</style>
</head>
<body>

<header class="site-header">
  <div class="brand abs">
    <span class="brand-mark"></span>
    <span class="brand-name">BEACON<br>ADVISORY</span>
  </div>
  <div class="contact-chip abs" style="left:380px">
    <span class="chip-icon"><svg width="8" height="11" viewBox="0 0 8 11"><rect x="1" y="0.5" width="6" height="10" rx="1" fill="none" stroke="#fff"/><rect x="2.5" y="2" width="3" height="5" fill="#fff"/></svg></span>
    <span><span class="chip-label">CALL US</span><span class="chip-value">+1 (555) 014 2290</span></span>
  </div>
  <div class="contact-chip abs" style="left:483px">
    <span class="chip-icon"><svg width="10" height="8" viewBox="0 0 10 8"><rect x="0.5" y="0.5" width="9" height="7" fill="none" stroke="#fff"/><polyline points="0.5,0.5 5,4.5 9.5,0.5" fill="none" stroke="#fff"/></svg></span>
    <span><span class="chip-label">EMAIL US</span><span class="chip-value">info@beaconadvisoryinc.com</span></span>
  </div>
</header>

<nav class="main-nav">
  <ul>
    <li class="active">HOME</li>
    <li style="left:146px;width:48px">ABOUT US</li>
    <li style="left:225px;width:48px">SERVICES</li>
    <li style="left:303px;width:56px">SOLUTIONS</li>
    <li style="left:390px;width:56px">RESOURCES</li>
    <li style="left:475px;width:46px">CAREER</li>
    <li style="left:548px;width:64px">CONTACT US</li>
  </ul>
  <span class="nav-sep" style="left:210px"></span>
  <span class="nav-sep" style="left:288px"></span>
  <span class="nav-sep" style="left:374px"></span>
  <span class="nav-sep" style="left:461px"></span>
  <span class="nav-sep" style="left:535px"></span>
</nav>

<section class="hero">
  <div class="hero-photo" role="img" aria-label="Photo of business consultants reviewing documents at a desk in a glass office"></div>
  <h2 class="hero-title">Delivers highest level of quality<br>consultants and services for the<br>lowest cost of ownership</h2>
  <span class="btn-more">READ MORE</span>
</section>

<section class="welcome">
  <h1>Welcome To Beacon Advisoryinc</h1>
  <span class="welcome-caret"></span>
  <p>Today's IT market is a dynamic, fast-paced industry, with ever-increasing demands. Meeting these demands for over 25 years, Beacon Advisory maintains a global presence, aggressively recruiting expertly qualified IT and Management Professionals from around the world and cultivating key partnerships with corporations to understand their business models end-to-end, with a goal of delivering exceptional client service and ensuring a consistent delivery....</p>
  <span class="welcome-toggle">+</span>
</section>

<section class="features">
  <div class="feature" style="left:62px">
    <svg width="110" height="110" viewBox="0 0 110 110" style="margin-top:38px">
      <polyline points="45,8 55,0 65,8" fill="none" stroke="#555" stroke-width="1"/>
      <polyline points="45,102 55,110 65,102" fill="none" stroke="#555" stroke-width="1" transform="translate(0,-6)"/>
      <polyline points="13,45 5,55 13,65" fill="none" stroke="#555" stroke-width="1" transform="translate(0,-12)"/>
      <polyline points="97,45 105,55 97,65" fill="none" stroke="#555" stroke-width="1" transform="translate(0,-12)"/>
      <g fill="#222" transform="translate(0,-12)">
        <circle cx="45" cy="48" r="3"/><circle cx="55" cy="46" r="3"/><circle cx="65" cy="48" r="3"/>
        <rect x="42" y="53" width="6" height="10"/><rect x="52" y="51" width="6" height="12"/><rect x="62" y="53" width="6" height="10"/>
        <rect x="40" y="63" width="30" height="3"/><rect x="45" y="66" width="3" height="4"/><rect x="62" y="66" width="3" height="4"/>
      </g>
    </svg>
    <h3 style="margin-top:-6px">CONSULTING</h3>
    <p>Beacon Advisory has certified professional consultants to work with you to help increase the business by providing IT services ...</p>
  </div>
  <div class="feature highlight" style="left:260px">
    <svg width="110" height="110" viewBox="0 0 110 110" style="margin-top:32px">
      <polyline points="45,0 55,8 65,0" fill="none" stroke="#1e9ad6" stroke-width="1"/>
      <polyline points="45,80 55,72 65,80" fill="none" stroke="#1e9ad6" stroke-width="1" transform="translate(0,6)"/>
      <polyline points="8,36 16,46 8,56" fill="none" stroke="#1e9ad6" stroke-width="1"/>
      <polyline points="102,36 94,46 102,56" fill="none" stroke="#1e9ad6" stroke-width="1"/>
      <circle cx="55" cy="46" r="9" fill="none" stroke="#1e9ad6" stroke-width="6" stroke-dasharray="4 3"/>
      <circle cx="55" cy="46" r="8" fill="none" stroke="#1e9ad6" stroke-width="4"/>
      <circle cx="55" cy="46" r="3" fill="#fff"/>
    </svg>
    <h3 style="margin-top:-13px">STAFF AUGMENTATION</h3>
    <p>For years Beacon Advisory as been offering our customers the ability to augment their existing staff..</p>
  </div>
  <div class="feature" style="left:445px">
    <svg width="110" height="110" viewBox="0 0 110 110" style="margin-top:38px">
      <polyline points="45,8 55,0 65,8" fill="none" stroke="#555" stroke-width="1"/>
      <polyline points="45,96 55,104 65,96" fill="none" stroke="#555" stroke-width="1"/>
      <polyline points="13,33 5,43 13,53" fill="none" stroke="#555" stroke-width="1"/>
      <polyline points="97,33 105,43 97,53" fill="none" stroke="#555" stroke-width="1"/>
      <rect x="42" y="30" width="26" height="26" rx="5" fill="#2a2a2a"/>
    </svg>
    <h3 style="margin-top:-6px">OFFSHORE</h3>
    <p>Our Offshore development model has a unique distinction of providing efficient software solutions ...</p>
  </div>
</section>

<section class="services">
  <h2 class="section-title" style="margin-top:13px">Our <span>Services</span></h2>
  <span class="title-rule" style="top:39px"></span>
  <span class="title-dot" style="top:35px"></span>
  <svg class="abs" style="left:28px;top:95px" width="16" height="30" viewBox="0 0 16 30"><polyline points="15,1 1,15 15,29" fill="none" stroke="#888"/></svg>
  <svg class="abs" style="left:634px;top:95px" width="16" height="30" viewBox="0 0 16 30"><polyline points="1,1 15,15 1,29" fill="none" stroke="#888"/></svg>
  <div class="service-card" style="left:61px">
    <div class="card-photo" role="img" aria-label="Photo of a hand touching glowing technology icons" style="background:linear-gradient(135deg,#1a1f26,#394656 55%,#c8a07f 80%,#2a3340)"></div>
    <div class="card-label">Technology</div>
  </div>
  <div class="service-card card-feature" style="left:257px">
    <h4>OFFSHORE</h4>
    <p>Our Offshore development model has a unique distinction of providing efficient software solutions with cost and quality advantage, using state-of-the-art</p>
    <span class="link">READ MORE »</span>
  </div>
  <div class="service-card" style="left:453px">
    <div class="card-photo" role="img" aria-label="Photo of a businessman selecting application icons on a blue screen" style="background:linear-gradient(120deg,#0e3f66,#2a7fb4 45%,#7aaecf 65%,#13395c)"></div>
    <div class="card-label">Application Developement</div>
  </div>
</section>

<section class="testimonial">
  <h2 class="section-title" style="margin-top:17px">Client <span>Testimonial</span></h2>
  <span class="title-rule" style="top:44px"></span>
  <span class="title-dot" style="top:40px"></span>
  <div class="avatar" role="img" aria-label="Portrait photo of the client"></div>
  <span class="quote-mark" style="left:152px;top:60px">“</span>
  <p class="quote">Lorem ipsum dolor sit amet, consectetuer adipiscing elit, sed diam nonummy nibh euismod tincidunt utvm laoreetm &nbsp;dolore magna aliquam erat volutpat. Ut wisi enim ad minim veniam, quis nostrud exerci tation ullamcorper suscipit lobortis nisl utmv aliquip ex ea commodo consequat. Duis autem vel eum iriure dolor in hendrerit in vulputate velit esse molestie consequat, velm illu dolore eu feugiat nulla facilisis at vero eros et accumsan etsto duis facilisi.</p>
  <span class="quote-mark" style="left:502px;top:110px">”</span>
  <span class="quote-rule"></span>
  <span class="author">- Miss Clara Newell</span>
  <span class="dots"><i class="on"></i><i></i><i></i><i></i></span>
</section>

<footer class="site-footer">
  <svg class="footer-wave" width="682" height="280" viewBox="0 0 682 280">
    <path d="M250,95 C360,110 470,100 560,70 C610,52 650,35 682,15 L682,40 C640,68 580,92 500,105 C420,116 330,110 250,95 Z" fill="#23b2ea"/>
    <path d="M0,85 C70,55 160,60 250,80 C360,105 470,108 560,88 C620,74 660,55 682,40 L682,280 L0,280 Z" fill="#1565b0"/>
  </svg>

  <div class="footer-col" style="left:60px">
    <h5>Quick Links</h5>
    <ul class="quick-links">
      <li>Home</li><li>About Us</li><li>Services</li><li>Resources</li><li>Contact Us</li>
    </ul>
  </div>
  <span class="col-divider" style="left:138px"></span>

  <div class="footer-col" style="left:161px">
    <h5>Contact Information</h5>
    <div class="contact-row"><svg width="7" height="10" viewBox="0 0 7 10"><path d="M3.5,0 A3.5,3.5 0 0 1 7,3.5 C7,6 3.5,10 3.5,10 C3.5,10 0,6 0,3.5 A3.5,3.5 0 0 1 3.5,0 Z" fill="#fff"/><circle cx="3.5" cy="3.5" r="1.3" fill="#1565b0"/></svg><span>420 Harbor Lane<br>Suite 12<br>Westfield, NJ 07090</span></div>
    <div class="contact-row"><svg width="8" height="8" viewBox="0 0 8 8"><path d="M1,0 L3,0 L3.5,2 L2.3,3 C3,4.5 3.8,5.3 5,5.8 L6,4.6 L8,5 L8,7 C8,7.6 7.5,8 7,8 C3,8 0,5 0,1 C0,0.5 0.4,0 1,0 Z" fill="#fff"/></svg><span>+1 (555) 014 2290</span></div>
    <div class="contact-row"><svg width="9" height="8" viewBox="0 0 9 8"><rect x="2" y="0" width="5" height="2.5" fill="#fff"/><rect x="0" y="3" width="9" height="3.5" rx="1" fill="#fff"/><rect x="2" y="5.5" width="5" height="2.5" fill="#fff"/></svg><span>555.019.4471</span></div>
    <div class="contact-row"><svg width="8" height="6" viewBox="0 0 8 6"><rect width="8" height="6" fill="#fff"/><polyline points="0,0 4,3.5 8,0" fill="none" stroke="#1565b0" stroke-width="0.8"/></svg><span>info@beaconmail.com</span></div>
  </div>
  <span class="col-divider" style="left:284px"></span>

  <div class="footer-col" style="left:310px">
    <h5>Quick Contact</h5>
    <span class="field">Name</span>
    <span class="field">Phone</span>
    <span class="field tall">Message</span>
    <span class="submit">SUBMIT</span>
  </div>
  <span class="col-divider" style="left:482px"></span>

  <div class="footer-brand">
    <span class="brand-mark" style="width:30px;height:30px"></span>
    <span class="brand-name" style="font-size:13px">BEACON<br>ADVISORY</span>
  </div>
  <div class="social" aria-label="Social links">
    <i style="background:#25467f"></i><i style="background:#3d9ad9"></i><i style="background:#1f7fc4"></i><i style="background:#f0a12d"></i>
  </div>

  <div class="copyright">Copyright © 2016 Beaconadvisoryinc. All Rights Reserved.</div>
</footer>

</body>
</html>
```